Web Developer Needs a Business Card Design

I need a personal business card design that represents me as a web developer for potential employers. I would like the background to be a dark color on the front for contrast with my logo and name. The back will have all my information along with a smaller version of the logo. I want something with a modern look and feel, not too conservative. This will be used for potential employers and freelance work.

Industry/Entity Type

Business

Contact Information for Business Card

Front should have my logo and name. The back should have all my personal information which would include: name: Tom Varulek, phone: 570-614-3098, email: tomvarulek@quillbox.net, website url: www.tomvarulek.net, logo, web developer.

Font styles to use
Sans Serif

Requirements
Must have
• Must include my logo. The color palette base color will be the logo color.

```html
<!DOCTYPE html>
<html lang="en">
<head>
<meta charset="utf-8">
<title>Tom Varulek — Business Card</title>
<link rel="stylesheet" href="https://fonts.googleapis.com/css2?family=Questrial&display=swap">
<style>
  :root {
    --canvas: #8b8d8c;
    --card: #e7e7e6;
    --band: #231f1e;
    --teal: #4fc9ad;
    --text-light: #dcdcdc;
  }
  * { margin: 0; padding: 0; box-sizing: border-box; }
  html, body { width: 1200px; height: 900px; overflow: hidden; }
  body {
    background: var(--canvas);
    font-family: "Questrial", "Century Gothic", sans-serif;
    display: flex;
    flex-direction: column;
    align-items: center;
    justify-content: center;
    gap: 60px;
  }
  .card {
    position: relative;
    width: 620px;
    height: 354px;
    background: var(--card);
    overflow: hidden;
  }
  .mark {
    position: absolute;
    border-radius: 50%;
    border: solid var(--teal);
    display: flex;
    align-items: center;
    justify-content: center;
    color: var(--teal);
    white-space: nowrap;
  }
  .card-front .mark {
    width: 160px; height: 160px;
    left: 230px; top: 97px;
    border-width: 7px;
    font-size: 21px;
  }
  .info-band {
    position: absolute;
    left: 0; top: 56px;
    width: 100%; height: 250px;
    background: var(--band);
  }
  .card-back .mark {
    width: 262px; height: 262px;
    left: 320px; top: 50px;
    border-width: 11px;
    outline: 4px solid var(--card);
    background: var(--card);
    font-size: 34px;
  }
  .identity {
    position: absolute;
    left: 36px; top: 74px;
  }
  .identity-name {
    color: var(--teal);
    font-size: 30px;
    line-height: 1.1;
  }
  .identity-role {
    color: var(--text-light);
    font-size: 18px;
    margin-top: 1px;
  }
  .contact-list {
    position: absolute;
    left: 40px; top: 144px;
    list-style: none;
  }
  .contact-item {
    display: flex;
    align-items: center;
    gap: 10px;
    height: 26px;
    color: var(--text-light);
    font-size: 15.5px;
    letter-spacing: 0.2px;
  }
  .contact-icon { width: 16px; height: 16px; flex: none; }
</style>
</head>
<body>
  <section class="card card-front" aria-label="Business card front">
    <div class="mark">Tom Varulek</div>
  </section>

  <section class="card card-back" aria-label="Business card back">
    <div class="info-band"></div>
    <div class="identity">
      <h1 class="identity-name">Tom Varulek</h1>
      <p class="identity-role">Front-End Developer</p>
    </div>
    <ul class="contact-list">
      <li class="contact-item">
        <svg class="contact-icon" viewBox="0 0 16 16" aria-hidden="true"><path fill="#4fc9ad" d="M3.2 1.5l2.3-.4 1.3 3.2-1.5 1.1a9 9 0 0 0 4.3 4.3l1.1-1.5 3.2 1.3-.4 2.3c-.2.9-1 1.4-1.9 1.3C6.3 12.6 2.4 8.7 1.9 3.4c-.1-.9.4-1.7 1.3-1.9z"/></svg>
        570-614-3098
      </li>
      <li class="contact-item">
        <svg class="contact-icon" viewBox="0 0 16 16" aria-hidden="true"><rect x="1" y="3.5" width="14" height="10" fill="#4fc9ad"/><path d="M1.5 4.2L8 9l6.5-4.8" fill="none" stroke="#231f1e" stroke-width="1.3"/></svg>
        tomvarulek@quillbox.net
      </li>
      <li class="contact-item">
        <svg class="contact-icon" viewBox="0 0 16 16" aria-hidden="true"><circle cx="8" cy="8" r="6.5" fill="none" stroke="#4fc9ad" stroke-width="1.6"/><ellipse cx="8" cy="8" rx="2.7" ry="6.5" fill="none" stroke="#4fc9ad" stroke-width="1.3"/><path d="M1.5 8h13" stroke="#4fc9ad" stroke-width="1.3"/></svg>
        www.tomvarulek.net
      </li>
      <li class="contact-item">
        <svg class="contact-icon" viewBox="0 0 16 16" aria-hidden="true"><circle cx="8" cy="8" r="6.5" fill="#4fc9ad"/></svg>
        @tomvarulek
      </li>
      <li class="contact-item">
        <svg class="contact-icon" viewBox="0 0 16 16" aria-hidden="true"><rect x="2" y="2" width="12" height="12" fill="#4fc9ad"/></svg>
        tomvarulek.net/profile
      </li>
      <li class="contact-item">
        <svg class="contact-icon" viewBox="0 0 16 16" aria-hidden="true"><circle cx="8" cy="8" r="6.5" fill="#4fc9ad"/></svg>
        tomvarulek.net/code
      </li>
    </ul>
    <div class="mark">Tom Varulek</div>
  </section>
</body>
</html>
```